Heritage Hollow Business Cards

Require a business card design. <br/><br/>Needs to include logo (either round or long version) plus these details:<br/>Maya Torvell<br/>Heritage Hollow<br/>maya@kelvadtrading.com.au<br/>02 6481 7395<br/>PO Box Glenwarra NSW 2791<br/>www.heritagehollow.com.au<br/><br/>I need in an editable format so that I can create for multiple staff members. <br/><br/>

Target Market(s)

We are an online store selling renovation products to home owners are builders. Looking for a classic classy design.

Industry/Entity Type

Home And Garden

Contact Information for Business Card

Maya Torvell
Heritage Hollow
maya@kelvadtrading.com.au
02 6481 7395
PO Box Glenwarra NSW 2791
www.heritagehollow.com.au

Colors

Designer to choose colors to be used in the design.

Requirements
Must have
• Must include Logo.

```html
<!DOCTYPE html>
<html lang="en">
<head>
<meta charset="utf-8">
<title>Heritage Hollow Business Cards</title>
<link href="https://fonts.googleapis.com/css2?family=Lora:wght@500&family=Roboto:wght@400;500;700&display=swap" rel="stylesheet">
<style>
  :root {
    --stage: #d9d9d9;
    --card-dark: #1e1e1f;
    --card-light: #ffffff;
    --ink: #1a1a1a;
    --ink-soft: #2b2b2b;
    --on-dark: #f2f2f2;
    --rule: #222222;
  }
  * { box-sizing: border-box; margin: 0; padding: 0; }
  html, body {
    width: 1200px; height: 1124px; overflow: hidden;
    background: var(--stage);
  }
  .sheet {
    position: relative; width: 1200px; height: 1124px;
    display: flex; flex-direction: column; align-items: center;
    justify-content: center; gap: 54px;
  }
  .card {
    position: relative; width: 840px; height: 480px;
    box-shadow: 0 10px 28px rgba(0,0,0,0.25);
  }
  .card--back { background: var(--card-dark); }
  .card--back .back-name {
    position: absolute; right: 70px; top: 250px;
    font-family: "Lora", serif; font-weight: 500;
    font-size: 34px; color: var(--on-dark); letter-spacing: 0.5px;
  }
  .card--front { background: var(--card-light); color: var(--ink); font-family: "Roboto", sans-serif; }
  .brand {
    position: absolute; right: 60px; top: 92px;
    display: flex; align-items: center; gap: 14px;
  }
  .brand-dot {
    width: 40px; height: 40px; border-radius: 50%;
    background: var(--ink);
  }
  .brand-name {
    font-family: "Roboto", sans-serif; font-weight: 500;
    font-size: 38px; color: var(--ink);
  }
  .person { position: absolute; left: 62px; top: 150px; }
  .person-name { font-size: 30px; font-weight: 700; color: var(--ink); }
  .person-company { font-size: 20px; font-weight: 400; color: var(--ink-soft); margin-top: 4px; }
  .divider {
    position: absolute; left: 58px; right: 56px; top: 240px;
    height: 2px; background: var(--rule);
  }
  .contacts {
    position: absolute; left: 58px; top: 278px; list-style: none;
    font-size: 21px; color: var(--ink-soft);
  }
  .contacts li { display: flex; align-items: center; gap: 14px; height: 36px; }
  .contacts svg { width: 18px; height: 18px; fill: none; stroke: var(--ink); stroke-width: 1.8; }
  .address {
    position: absolute; right: 60px; bottom: 52px; text-align: right;
    font-size: 22px; line-height: 1.3; color: var(--ink-soft);
  }
</style>
</head>
<body>
<main class="sheet">
  <section class="card card--back" aria-label="Card back">
    <p class="back-name">Heritage Hollow</p>
  </section>

  <section class="card card--front" aria-label="Card front">
    <div class="brand">
      <span class="brand-dot"></span>
      <span class="brand-name">Heritage Hollow</span>
    </div>
    <div class="person">
      <h1 class="person-name">Maya Torvell</h1>
      <p class="person-company">Heritage Hollow</p>
    </div>
    <div class="divider"></div>
    <ul class="contacts">
      <li>
        <svg viewBox="0 0 24 24" aria-hidden="true"><path d="M5 3h4l2 5-2.5 1.5a11 11 0 0 0 6 6L16 13l5 2v4a2 2 0 0 1-2 2A17 17 0 0 1 3 5a2 2 0 0 1 2-2z" fill="#1a1a1a" stroke="none"/></svg>
        <span>02 6481 7395</span>
      </li>
      <li>
        <svg viewBox="0 0 24 24" aria-hidden="true"><rect x="3" y="5" width="18" height="14" rx="1"/><path d="M3 6l9 7 9-7"/></svg>
        <span>maya@kelvadtrading.com.au</span>
      </li>
      <li>
        <svg viewBox="0 0 24 24" aria-hidden="true"><circle cx="12" cy="12" r="9"/><path d="M3 12h18M12 3c3 3 3 15 0 18M12 3c-3 3-3 15 0 18"/></svg>
        <span>www.heritagehollow.com.au</span>
      </li>
    </ul>
    <p class="address">PO Box Glenwarra<br>NSW 2791</p>
  </section>
</main>
</body>
</html>
```